Business Card for: Bramwell Financial Advisory Services Inc.

provide strategic financial advisory services to companies in the areas of corporate finance, mergers and acquisitions, executive coaching and strategic planning

Target Market(s)

Companies, banks, accountants, lawyers

Industry/Entity Type

High end business consulting in corporate finance, mergers and acquisitions, consulting

Contact Information for Business Card

Name of company, Name: xxxxxx xxxxxx , CEO, - phone number: 1-xxx-xxx-xxxx, - email address,

Requirements
Must have
• Must be professional and simple.
Nice to have
• simple, straight graphics, must give the impression that we are trustworthy, professional, competent
Should not have
• loud colors, loud design features

```html
<!DOCTYPE html>
<html lang="en">
<head>
<meta charset="utf-8">
<title>Bramwell Financial Advisory Services Inc. – Business Card</title>
<link href="https://fonts.googleapis.com/css2?family=Tinos:wght@400;700&display=swap" rel="stylesheet">
<style>
  :root {
    --backdrop: #9a9a9a;
    --paper: #ffffff;
    --navy: #002868;
    --name-ink: #3b3468;
    --ink: #111111;
    --reverse-ink: #e9e9ec;
  }
  * { box-sizing: border-box; margin: 0; padding: 0; }
  html, body {
    width: 1200px; height: 1059px; overflow: hidden;
    background: var(--backdrop);
    font-family: "Tinos", "Times New Roman", serif;
  }
  .canvas { position: relative; width: 1200px; height: 1059px; }
  .card { position: absolute; border-radius: 30px; overflow: hidden; }

  .card-front { left: 259px; top: 85px; width: 698px; height: 398px; background: var(--paper); }
  .brand {
    position: absolute; right: 40px; top: 60px; text-align: right;
    color: var(--navy); font-weight: 700; line-height: 1;
  }
  .brand-main { display: block; font-size: 42px; letter-spacing: 2px; text-transform: uppercase; }
  .brand-sub { display: block; font-size: 15.5px; letter-spacing: 1px; margin-top: 8px; text-transform: uppercase; }

  .holder-name { position: absolute; left: 41px; top: 280px; transform: translateY(-100%); font-size: 26px; line-height: 1.2; font-weight: 700; color: var(--name-ink); top: 225px; }
  .holder-title { position: absolute; left: 41px; top: 230px; font-size: 17px; line-height: 1.2; color: var(--ink); }
  .divider { position: absolute; left: 40px; top: 268px; width: 619px; height: 1.5px; background: var(--ink); }

  .contact-list { position: absolute; left: 40px; top: 284px; list-style: none; }
  .contact-item { display: flex; align-items: center; height: 29.5px; font-size: 17px; color: var(--ink); white-space: nowrap; }
  .contact-icon { width: 18px; height: 18px; margin-right: 17px; fill: var(--navy); flex: none; }

  .address { position: absolute; right: 40px; top: 308px; text-align: right; font-size: 17px; line-height: 25px; color: var(--ink); font-style: normal; white-space: nowrap; }

  .card-back {
    left: 254px; top: 566px; width: 714px; height: 407px; background: var(--navy);
    display: flex; align-items: center; justify-content: center;
  }
  .card-back .brand { position: static; text-align: center; color: var(--reverse-ink); }
  .card-back .brand-main { font-size: 54px; letter-spacing: 3px; }
  .card-back .brand-sub { font-size: 20px; letter-spacing: 1.5px; margin-top: 12px; }
</style>
</head>
<body>
<main class="canvas">
  <section class="card card-front" aria-label="Card front">
    <div class="brand">
      <span class="brand-main">Bramwell</span>
      <span class="brand-sub">Financial Advisory Services Inc.</span>
    </div>

    <h1 class="holder-name">Daniel Hartley</h1>
    <p class="holder-title">CEO</p>
    <div class="divider"></div>

    <ul class="contact-list">
      <li class="contact-item">
        <svg class="contact-icon" viewBox="0 0 24 24" aria-hidden="true"><path d="M6.6 10.8a15.1 15.1 0 0 0 6.6 6.6l2.2-2.2a1 1 0 0 1 1-.25 11.4 11.4 0 0 0 3.6.57 1 1 0 0 1 1 1V20a1 1 0 0 1-1 1A17 17 0 0 1 3 4a1 1 0 0 1 1-1h3.5a1 1 0 0 1 1 1c0 1.250.2 2.45.57 3.57a1 1 0 0 1-.25 1z"/></svg>
        1-416-555-0142
      </li>
      <li class="contact-item">
        <svg class="contact-icon" viewBox="0 0 24 24" aria-hidden="true"><path d="M2 5h20v2l-10 6L2 7z"/><path d="M2 9l10 6 10-6v10H2z"/></svg>
        dhartley@bramwell.com
      </li>
      <li class="contact-item">
        <svg class="contact-icon" viewBox="0 0 24 24" aria-hidden="true"><circle cx="12" cy="12" r="10"/><path d="M8 5c2 1 1 3 3 3s1 3-1 3-3 1-2 3 0 3-1 4M15 4c-1 2 1 3 2 2s2 2 3 3M14 14c2-1 4 0 4 2s-2 3-3 4" fill="none" stroke="#fff" stroke-width="1.6"/></svg>
        www.bramwelladvisory.com
      </li>
    </ul>

    <address class="address">
      88 Harbour Street, Suite 400<br>
      Toronto, ON M5J 2G2
    </address>
  </section>

  <section class="card card-back" aria-label="Card back">
    <div class="brand">
      <span class="brand-main">Bramwell</span>
      <span class="brand-sub">Financial Advisory Services Inc.</span>
    </div>
  </section>
</main>
</body>
</html>
```